Simple and Clean business card design

We would like the design to be simple clean and to incorporate our colors.

We are open to your design and talent, we have the dots in our logo as we think of it as data points and we connect data points for people.

We are open to see the great creative and clean design you bring to the table

Contact Information for Business Card

please include: name, position, email, phone and website

Font styles to use
Sans Serif

Requirements
Must have
• my colors incorporated, simplicity
Nice to have
• lots of white space, simplicity
Should not have
• complexicity/ complex art

```html
<!DOCTYPE html>
<html lang="en">
<head>
<meta charset="utf-8">
<title>Nectara Business Card</title>
<link rel="stylesheet" href="https://fonts.googleapis.com/css2?family=Montserrat:wght@300;400;700&display=swap">
<style>
  :root {
    --backdrop: #e9eeec;
    --card-white: #ffffff;
    --card-mint: #80dcc0;
    --card-mint-soft: #8fd9c4;
    --ink: #111111;
    --ink-soft: #555555;
    --contact-ink: #333333;
    --icon-ink: #444444;
    --brand-blue: #1a86e8;
  }
  * { box-sizing: border-box; margin: 0; padding: 0; }
  html, body { width: 1200px; height: 1200px; overflow: hidden; }
  body {
    background: var(--backdrop);
    font-family: "Montserrat", sans-serif;
    color: var(--ink);
    display: flex;
    flex-direction: column;
    align-items: center;
    justify-content: center;
    gap: 56px;
  }
  .card {
    position: relative;
    width: 880px;
    height: 503px;
    border-radius: 36px;
    overflow: hidden;
    box-shadow: 0 10px 30px rgba(0,0,0,0.12);
  }
  .card--front { background: var(--card-white); }
  .card--back { background: var(--card-mint); }

  .wordmark {
    position: absolute;
    font-family: "Montserrat", sans-serif;
    font-weight: 400;
    color: var(--ink);
    line-height: 1;
    letter-spacing: 1px;
    white-space: nowrap;
  }
  .card--front .wordmark { left: 64px; top: 80px; font-size: 104px; }
  .card--back .wordmark { left: 50%; top: 50%; transform: translate(-50%, -50%); font-size: 124px; }

  .holder {
    position: absolute;
    left: 430px;
    top: 215px;
  }
  .holder__name {
    font-size: 34px;
    font-weight: 700;
    letter-spacing: 0.5px;
    line-height: 1.1;
    white-space: nowrap;
  }
  .holder__name .first { color: var(--brand-blue); }
  .holder__role {
    font-size: 20px;
    font-weight: 300;
    color: var(--ink-soft);
    letter-spacing: 1px;
    margin-top: 2px;
  }
  .contacts {
    position: absolute;
    left: 380px;
    top: 320px;
    list-style: none;
    display: flex;
    flex-direction: column;
    gap: 12px;
  }
  .contacts__item {
    display: flex;
    align-items: center;
    gap: 22px;
    font-size: 23px;
    font-weight: 400;
    color: var(--contact-ink);
    white-space: nowrap;
  }
  .contacts__icon { width: 16px; height: 16px; flex: none; fill: var(--icon-ink); }

  .back-surface {
    position: absolute;
    inset: 0;
    background: linear-gradient(135deg, var(--card-mint-soft) 0%, var(--card-mint) 50%, var(--card-mint-soft) 100%);
  }
</style>
</head>
<body>
  <section class="card card--front" aria-label="Card front">
    <div class="wordmark">nectara</div>

    <div class="holder">
      <p class="holder__name"><span class="first">NECTARA</span> SAMPLE</p>
      <p class="holder__role">CEO</p>
    </div>

    <ul class="contacts">
      <li class="contacts__item">
        <svg class="contacts__icon" viewBox="0 0 16 16" aria-hidden="true"><path d="M8 0a5.5 5.5 0 0 0-5.5 5.5C2.5 10 8 16 8 16s5.5-6 5.5-10.5A5.5 5.5 0 0 0 8 0zm0 7.5a2 2 0 1 1 0-4 2 2 0 0 1 0 4z"/></svg>
        <span>LANTERN, USA 00041</span>
      </li>
      <li class="contacts__item">
        <svg class="contacts__icon" viewBox="0 0 16 16" aria-hidden="true"><path d="M0 3h16v10H0z M1.5 4.5 8 9l6.5-4.5" fill="#444" stroke="#fff" stroke-width="1"/></svg>
        <span>hello@nectara.com</span>
      </li>
      <li class="contacts__item">
        <svg class="contacts__icon" viewBox="0 0 16 16" aria-hidden="true"><path d="M3.6 0.8 6 3.6 4.7 5.4c.9 2.2 3.6 5 5.9 5.9l1.8-1.3 2.8 2.4-1.7 2.6C7.5 14.8 1.2 8.5 1 2.5z"/></svg>
        <span>000 111222</span>
      </li>
      <li class="contacts__item">
        <svg class="contacts__icon" viewBox="0 0 16 16" aria-hidden="true"><g fill="none" stroke="#444" stroke-width="1.3"><circle cx="8" cy="8" r="7"/><ellipse cx="8" cy="8" rx="3" ry="7"/><path d="M1 8h14M2.5 4h11M2.5 12h11"/></g></svg>
        <span>www.nectara.com</span>
      </li>
    </ul>
  </section>

  <section class="card card--back" aria-label="Card back">
    <div class="back-surface" role="img" aria-label="Decorative pattern of soft translucent circles on a mint background"></div>
    <div class="wordmark">nectara</div>
  </section>
</body>
</html>
```